Web design for sitter site

We will be launching a sitter site in the coming months that focuses on sitters for children. The name of this site will be NestWatch.com
We will need:
1. main page design
2. site logo designed
3. subpages as well for the look of people's profiles, and job listings, etc (see links below)
We only need the design, photos, font files, etc. We do not need this site coded (no html), a ps job is fine.
Some competing sites in the space include - tendlane.com and brio.com
http://www.pebble-keeper.example/images/profile1.jpg
http://marrowbooks.example/wp-content/uploads/2013/09/brio-review.png
http://www.quillmont.example/hr/photos/tend_lane2.jpg
Thanks for your interest!
Mothers of children, mainly women
Online

```html
<!DOCTYPE html>
<html lang="en">
<head>
<meta charset="utf-8">
<title>NestWatch – Find a Sitter</title>
<link href="https://fonts.googleapis.com/css2?family=Open+Sans:wght@400;600;700&family=Roboto+Condensed:wght@700&family=Tinos&display=swap" rel="stylesheet">
<style>
:root{
  --blue:#1b4ba8;
  --blue-dark:#0f3478;
  --blue-text:#1c55b0;
  --navy:#0d2c66;
  --grey-text:#6a6a6a;
  --dark-text:#333;
  --panel:rgba(110,110,110,.72);
  --footer:#1e1e1e;
  --footer-bottom:#141414;
  --footer-text:#a9a9a9;
  --white:#fff;
}
*{margin:0;padding:0;box-sizing:border-box}
html,body{width:702px;height:1200px;overflow:hidden;background:var(--white)}
body{position:relative;font-family:"Open Sans",Arial,sans-serif;color:var(--dark-text)}
.abs{position:absolute}
.site-header{left:0;top:0;width:702px;height:54px;background:var(--blue)}
.brand{left:58px;top:11px;font-size:22px;font-weight:600;color:var(--white)}
.nav a{position:absolute;top:19px;height:16px;line-height:16px;font-size:8.5px;color:var(--white);text-decoration:none;padding:0 6px}
.nav a.active{background:var(--blue-dark)}
.nav a.login{background:var(--navy);top:17px;height:19px;line-height:19px;padding:0 10px;font-weight:600}
.hero{left:0;top:54px;width:702px;height:334px;background:linear-gradient(100deg,#8ca34b 0%,#b7c56a 30%,#d9d98a 55%,#9fb24e 80%,#6f8c34 100%)}
.hero-arrow{width:28px;height:28px;border-radius:50%;background:rgba(90,90,90,.55);top:203px}
.signup{left:305px;top:72px;width:339px;height:300px;background:var(--panel)}
.signup h2{position:absolute;left:0;top:14px;width:100%;text-align:center;color:var(--white);font-size:12.5px;font-weight:600;line-height:21px;letter-spacing:.2px}
.toggle{left:78px;top:66px;width:175px;height:23px;background:#6d7580}
.toggle .parent{position:absolute;left:0;top:0;width:69px;height:23px;background:var(--blue);color:var(--white);font-size:8px;font-weight:600;line-height:23px;padding-left:9px}
.toggle .care{position:absolute;right:9px;top:0;line-height:23px;font-size:8px;color:#c9ccd0}
.toggle .or{position:absolute;left:65px;top:-6px;width:34px;height:34px;border-radius:50%;background:var(--blue);color:var(--white);font-size:8.5px;font-weight:700;text-align:center;line-height:34px}
.form{left:13px;top:114px;width:314px;height:173px;background:rgba(255,255,255,.86)}
.form h3{position:absolute;top:9px;width:100%;text-align:center;font-size:10px;font-weight:600;color:#7a7a7a}
.form label{position:absolute;font-size:6.5px;font-weight:600;color:#9a9a9a}
.form .field{position:absolute;width:128px;height:23px;background:var(--white);border:1px solid #d3d3d3}
.join{right:14px;top:134px;width:66px;height:22px;background:var(--blue);color:var(--white);font-size:8.5px;font-weight:600;text-align:center;line-height:22px}
.dot{top:395px;width:6px;height:6px;border-radius:50%;background:#c8c8c8}
.dot.on{background:var(--blue)}
.section-title{left:0;width:702px;text-align:center;font-size:22px;color:var(--blue-text)}
.section-lead{left:120px;width:462px;text-align:center;font-size:8.5px;line-height:12px;color:var(--grey-text)}
.step-line{top:537px;height:2px;background:var(--blue)}
.diamond{top:506px;width:64px;height:64px}
.chev{top:527px}
.step-title{width:180px;text-align:center;font-size:13px;line-height:14px;color:var(--blue-text)}
.step-title.dark{color:var(--dark-text)}
.step-title b{font-weight:600}
.step-desc{width:180px;text-align:center;font-size:7.8px;line-height:12px;color:#555}
.read-more{left:102px;top:650px;width:60px;height:16px;border-radius:5px;background:var(--blue);color:var(--white);font-size:7.5px;text-align:center;line-height:16px;box-shadow:0 2px 0 var(--navy)}
.tile{top:771px;width:188px;height:99px}
.tile.offer{background:var(--blue);color:var(--white);font-size:9.8px;line-height:13px;text-align:center;padding:20px 14px 0}
.get-started{left:61px;top:71px;width:68px;height:16px;background:var(--navy);font-size:7.5px;font-weight:600;line-height:16px}
.avatar{top:949px;width:44px;height:44px;border-radius:50%;background:#e9e9e9;border:3px solid #f6f6f6;box-shadow:0 0 0 1px #ddd}
.quote-mark{top:957px}
.quote{width:124px;font-family:"Tinos",serif;font-size:7.8px;line-height:10.8px;text-align:justify;color:var(--dark-text)}
.quote-name{font-family:"Tinos",serif;font-size:8px;font-weight:700;color:#222}
.quote-role{font-size:5.5px;color:#888}
.quote-role span{color:var(--blue-text)}
.site-footer{left:0;top:1043px;width:702px;height:123px;background:var(--footer)}
.footer-bottom{left:0;top:1166px;width:702px;height:34px;background:var(--footer-bottom);text-align:center;font-size:7.5px;line-height:34px;color:#888}
.footer-bottom span{color:var(--blue-text)}
.fcol{top:1064px;width:101px}
.fcol h4{font-family:"Roboto Condensed",sans-serif;font-size:8.5px;color:#ddd;padding-bottom:4px;border-bottom:1px solid #444;margin-bottom:6px}
.fcol li{list-style:none;font-size:7.3px;line-height:13px;color:var(--footer-text);letter-spacing:.3px}
.fcol li::before{content:"• ";font-size:6px}
.fcol li.current{color:var(--blue-text)}
.fcol.social li::before{content:"";display:inline-block;width:9px;height:9px;border-radius:50%;background:#777;margin-right:7px;vertical-align:-1px}
.fcol.social li:first-child::before{background:var(--blue)}
.fcol.social li{line-height:14px}
</style>
</head>
<body>

<header class="abs site-header">
  <div class="abs brand">NestWatch</div>
  <nav class="nav">
    <a class="active" style="left:262px">How It Works</a>
    <a style="left:340px">Child Care</a>
    <a style="left:405px">Senior Care</a>
    <a style="left:476px">Pet Care</a>
    <a style="left:537px">Contact Us</a>
    <a class="login" style="left:599px">LOGIN</a>
  </nav>
</header>

<section class="abs hero" role="img" aria-label="Photo of a smiling older man sitting in a sunny meadow with his golden retriever"></section>
<svg class="abs hero-arrow" style="left:19px" viewBox="0 0 28 28"><circle cx="14" cy="14" r="14" fill="rgba(80,80,80,.5)"/><path d="M16 8l-6 6 6 6" stroke="#fff" stroke-width="2.5" fill="none"/></svg>
<svg class="abs hero-arrow" style="left:652px" viewBox="0 0 28 28"><circle cx="14" cy="14" r="14" fill="rgba(255,255,255,.35)"/><path d="M12 8l6 6-6 6" stroke="#fff" stroke-width="2.5" fill="none"/></svg>

<div class="abs signup">
  <h2>SIGN UP TO START YOUR FREE SITTER<br>SEARCH.</h2>
  <div class="abs toggle">
    <div class="parent">I'am a Parent</div>
    <div class="care">I'am a Caregiver</div>
    <div class="or">OR</div>
  </div>
  <div class="abs form">
    <h3>Signup to your acount</h3>
    <label style="left:13px;top:40px">User Name</label>
    <div class="field" style="left:12px;top:51px"></div>
    <label style="left:172px;top:40px">Email Address</label>
    <div class="field" style="left:171px;top:51px"></div>
    <label style="left:13px;top:87px">Zip Code or City Name</label>
    <div class="field" style="left:12px;top:99px"></div>
    <label style="left:172px;top:89px">Password</label>
    <div class="field" style="left:171px;top:99px"></div>
    <div class="abs join">Join Now</div>
  </div>
</div>

<div class="abs dot on" style="left:330px"></div>
<div class="abs dot" style="left:340px"></div>
<div class="abs dot" style="left:351px"></div>

<h2 class="abs section-title" style="top:428px">See how it works</h2>
<p class="abs section-lead" style="top:462px">simply dummy text of the printing and typesetting industry. Lorem Ipsum has been the industry's standard dummy text ever since the 1500s, when an unknown printer took a galley of type and scrambled</p>

<div class="abs step-line" style="left:67px;width:129px"></div>
<div class="abs step-line" style="left:280px;width:129px"></div>
<div class="abs step-line" style="left:505px;width:129px"></div>

<svg class="abs diamond" style="left:98px" viewBox="0 0 64 64"><rect x="13" y="13" width="38" height="38" rx="3" transform="rotate(45 32 32)" fill="var(--blue)"/><rect x="25" y="22" width="14" height="18" fill="none" stroke="#fff" stroke-width="1.8"/><path d="M28 27h8M28 31h8M28 35h5" stroke="#fff" stroke-width="1.4"/><path d="M35 40l6-8" stroke="#fff" stroke-width="2"/></svg>
<svg class="abs diamond" style="left:312px" viewBox="0 0 64 64"><rect x="13" y="13" width="38" height="38" rx="3" transform="rotate(45 32 32)" fill="var(--blue)"/><circle cx="34" cy="27" r="4.5" fill="#fff"/><path d="M26 40c0-6 4-9 8-9s8 3 8 9z" fill="#fff"/><circle cx="27" cy="29" r="3.5" fill="#fff"/><path d="M21 40c0-5 3-7 6-7" stroke="#fff" stroke-width="2" fill="none"/></svg>
<svg class="abs diamond" style="left:538px" viewBox="0 0 64 64"><rect x="13" y="13" width="38" height="38" rx="3" transform="rotate(45 32 32)" fill="var(--blue)"/><path d="M32 41l-8-8a4.5 4.5 0 0 1 8-5 4.5 4.5 0 0 1 8 5z" fill="#fff"/></svg>

<svg class="abs chev" style="left:231px" width="14" height="22" viewBox="0 0 14 22"><path d="M2 2l9 9-9 9" stroke="var(--blue)" stroke-width="2.5" fill="none"/></svg>
<svg class="abs chev" style="left:449px" width="14" height="22" viewBox="0 0 14 22"><path d="M2 2l9 9-9 9" stroke="var(--blue)" stroke-width="2.5" fill="none"/></svg>

<div class="abs step-title" style="left:38px;top:586px"><b>Parents</b><br>Post Your Job</div>
<div class="abs step-title dark" style="left:251px;top:586px"><b>Caregivers</b><br>Apply to Jobs</div>
<div class="abs step-title dark" style="left:477px;top:586px">Find the Right Match</div>

<p class="abs step-desc" style="left:38px;top:619px">Sign up for a host account and establish your brand and event on Keplo.</p>
<p class="abs step-desc" style="left:251px;top:619px">Sign up for a host account and establish your brand and event on Keplo.</p>
<p class="abs step-desc" style="left:477px;top:619px">Sign up for a host account and establish your brand and event on Keplo.</p>
<div class="abs read-more">Read More</div>

<h2 class="abs section-title" style="top:685px">Explore what we offer</h2>
<p class="abs section-lead" style="top:720px">simply dummy text of the printing and typesetting industry. Lorem Ipsum has been the industry's standard dummy text ever since the 1500s, when an unknown printer took a galley of type and scrambled</p>

<div class="abs tile" style="left:58px;background:linear-gradient(180deg,#9fbf6a,#6f9a3a 70%,#5a8a2c)" role="img" aria-label="Photo of a smiling toddler crawling on green grass"></div>
<div class="abs tile offer" style="left:258px">Senior Housing &nbsp;&nbsp;Home Care Agencies &nbsp;&nbsp;Home Care Individuals &nbsp;&nbsp;Special Needs Caregivers &nbsp;&nbsp;Senior Care Planning
  <div class="abs get-started">GET STARTED</div>
</div>
<div class="abs tile" style="left:457px;background:linear-gradient(180deg,#f2b8d2,#e89cc0)" role="img" aria-label="Photo of a small terrier with a pink bow in a pink bath tub"></div>

<h2 class="abs section-title" style="top:902px">Testimonials</h2>

<div class="abs avatar" style="left:58px" role="img" aria-label="Portrait of a customer"></div>
<div class="abs avatar" style="left:261px" role="img" aria-label="Portrait of a customer"></div>
<div class="abs avatar" style="left:460px" role="img" aria-label="Portrait of a customer"></div>

<svg class="abs quote-mark" style="left:119px" width="24" height="18" viewBox="0 0 24 18"><path d="M0 18V9Q0 2 9 0v4Q5 5 5 9h4v9zM13 18V9q0-7 9-9v4q-4 1-4 5h4v9z" fill="#ddd"/></svg>
<svg class="abs quote-mark" style="left:322px" width="24" height="18" viewBox="0 0 24 18"><path d="M0 18V9Q0 2 9 0v4Q5 5 5 9h4v9zM13 18V9q0-7 9-9v4q-4 1-4 5h4v9z" fill="#ddd"/></svg>
<svg class="abs quote-mark" style="left:521px" width="24" height="18" viewBox="0 0 24 18"><path d="M0 18V9Q0 2 9 0v4Q5 5 5 9h4v9zM13 18V9q0-7 9-9v4q-4 1-4 5h4v9z" fill="#ddd"/></svg>

<p class="abs quote" style="left:119px;top:969px">&emsp;&emsp;&emsp;&ensp;Pellentesque et pulvinar enim. Quisque at tempor ligula. Donec ut purus sed tortor malesuada.</p>
<p class="abs quote" style="left:322px;top:969px">&emsp;&emsp;&emsp;&ensp;Pellentesque et pulvinar enim. Quisque at tempor ligula. Donec ut purus sed tortor malesuada.</p>
<p class="abs quote" style="left:521px;top:969px">&emsp;&emsp;&emsp;&ensp;Pellentesque et pulvinar enim. Quisque at tempor ligula. Donec ut purus sed tortor malesuada.</p>

<div class="abs quote-name" style="left:119px;top:1005px">Rowan Ellery</div>
<div class="abs quote-name" style="left:322px;top:1005px">Rowan Ellery</div>
<div class="abs quote-name" style="left:521px;top:1005px">Rowan Ellery</div>
<div class="abs quote-role" style="left:119px;top:1018px">Art Director / <span>lorem ipsum</span></div>
<div class="abs quote-role" style="left:322px;top:1018px">Art Director / <span>lorem ipsum</span></div>
<div class="abs quote-role" style="left:521px;top:1018px">Art Director / <span>lorem ipsum</span></div>

<footer class="abs site-footer"></footer>
<div class="abs fcol" style="left:62px"><h4>COMPANY</h4><ul><li class="current">About Us</li><li>Delivery Information</li><li>Privacy Policy</li><li>Terms &amp; Conditions</li></ul></div>
<div class="abs fcol" style="left:181px"><h4>FOR PETS</h4><ul><li>Pet Care</li><li>Pet Sitters</li></ul></div>
<div class="abs fcol" style="left:298px"><h4>FOR CHILDREN</h4><ul><li>Child Care</li><li>Babysitters</li></ul></div>
<div class="abs fcol" style="left:417px"><h4>FOR ADULTS &amp; SENIORS</h4><ul><li>Senior Care</li><li>Home Care</li></ul></div>
<div class="abs fcol social" style="left:543px"><h4>FOLLOW US</h4><ul><li>Murmur</li><li>Orbit</li><li>Kinfolk</li></ul></div>
<div class="abs footer-bottom">© 2014, <span>Yoursite</span>. All rights reserved.</div>

</body>
</html>
```